Business Card For Halvenmoor Financial Consulting

Hi, I would like a business card designed. Bold, modern.
Please use the same design as the logo. I have also attached the website design to see the overall theme.
Wordmark Font
Color: Hex: #01AEF7

```html
<!DOCTYPE html>
<html lang="en">
<head>
<meta charset="utf-8">
<title>Halvenmoor Financial Consulting – Business Card</title>
<link href="https://fonts.googleapis.com/css2?family=Montserrat:wght@800&family=Inter:wght@400;500&display=swap" rel="stylesheet">
<style>
  :root {
    --navy: #0b3a66;
    --navy-deep: #083158;
    --sky: #01aef7;
    --sky-soft: #3aa6e0;
    --ink: #2b2f36;
    --paper: #ffffff;
    --stage: #24282d;
  }
  html, body {
    margin: 0;
    width: 1200px;
    height: 900px;
    overflow: hidden;
    background: var(--stage);
  }
  .card {
    position: absolute;
    left: 180px;
    top: 210px;
    width: 840px;
    height: 480px;
    background: var(--paper);
    overflow: hidden;
    box-shadow: 0 18px 40px rgba(0,0,0,.45);
  }
  .card__wave {
    position: absolute;
    inset: 0;
    width: 100%;
    height: 100%;
  }
  .brand {
    position: absolute;
    left: 60px;
    top: 128px;
    display: flex;
    align-items: center;
    gap: 14px;
  }
  .brand__square {
    width: 44px;
    height: 44px;
    background: var(--sky);
    flex: none;
  }
  .brand__name {
    font-family: "Montserrat", sans-serif;
    font-weight: 800;
    color: var(--navy);
    text-transform: uppercase;
    margin: 0;
  }
  .brand__main {
    display: block;
    font-size: 34px;
    line-height: 1;
    letter-spacing: 1px;
  }
  .brand__sub {
    display: block;
    margin-top: 6px;
    font-size: 12px;
    line-height: 1;
    letter-spacing: 4.2px;
  }
  .divider {
    position: absolute;
    left: 456px;
    top: 120px;
    width: 2px;
    height: 230px;
    background: var(--navy);
  }
  .contact {
    position: absolute;
    left: 482px;
    top: 118px;
    width: 330px;
    font-family: "Inter", sans-serif;
    color: var(--ink);
  }
  .contact__name {
    font-family: "Montserrat", sans-serif;
    font-weight: 800;
    font-size: 28px;
    line-height: 1.1;
    color: var(--navy);
    margin: 0;
    text-transform: uppercase;
    letter-spacing: .5px;
  }
  .contact__title {
    margin: 4px 0 18px;
    font-size: 18px;
    line-height: 1.2;
    color: var(--sky-soft);
  }
  .contact__address {
    margin: 0 0 14px;
    font-size: 17px;
    line-height: 1.3;
  }
  .contact__list {
    list-style: none;
    padding: 0;
    margin: 0;
    font-size: 17px;
    line-height: 1.45;
  }
  .contact__list li {
    display: flex;
    align-items: center;
    gap: 8px;
  }
  .contact__icon {
    width: 14px;
    height: 14px;
    fill: var(--sky-soft);
    flex: none;
  }
</style>
</head>
<body>
  <article class="card">
    <svg class="card__wave" viewBox="0 0 840 480" preserveAspectRatio="none" aria-hidden="true">
      <path d="M0 262 C 180 268, 330 360, 520 420 C 620 452, 700 468, 780 480 L0 480 Z" fill="var(--navy-deep)"/>
      <path d="M0 250 C 180 256, 330 348, 520 410 C 620 442, 700 460, 790 480" fill="none" stroke="var(--sky-soft)" stroke-width="6"/>
    </svg>

    <div class="brand">
      <span class="brand__square"></span>
      <p class="brand__name">
        <span class="brand__main">Halvenmoor</span>
        <span class="brand__sub">Financial Consulting</span>
      </p>
    </div>

    <div class="divider"></div>

    <div class="contact">
      <h1 class="contact__name">Marlen Ostrick</h1>
      <p class="contact__title">President</p>
      <p class="contact__address">18420 Coral Bay Drive<br>Seabrook CA 92714</p>
      <ul class="contact__list">
        <li>
          <svg class="contact__icon" viewBox="0 0 16 16"><path d="M3.5 1.5l2.5 3-1.6 1.7c.8 1.8 2.3 3.3 4.1 4.1L10.2 8.7l3 2.5-1.4 2.8C6.5 14 2 9.5 1 4.2z"/></svg>
          555-014-2270
        </li>
        <li>
          <svg class="contact__icon" viewBox="0 0 16 16"><path d="M1 3h14v10H1z M1 3l7 5 7-5" stroke="#fff" stroke-width="1"/></svg>
          info@HalvenmoorConsulting.com
        </li>
        <li>
          <svg class="contact__icon" viewBox="0 0 16 16"><circle cx="8" cy="8" r="7"/><path d="M1 8h14M8 1c-3 3-3 11 0 14M8 1c3 3 3 11 0 14" stroke="#fff" stroke-width="1" fill="none"/></svg>
          www.HalvenmoorConsulting.com
        </li>
      </ul>
    </div>
  </article>
</body>
</html>
```